Harborlight Plans (03)

We're designing a website to sell Medicare Supplements. Attached is the script we want to say and general layout, but please use your best knowledge to make it better. This platform should be extremely user-friendly, but we want to make it look fun and approachable! Most Insurance/medicare websites are very boring, drab, simple but we want this one to be more personalized, fun and sexy (but again, still user-friendly since our target demographic is 65+).

This homepage should include a fun and inviting quiz, the script is in the attachment below. It should also include the blurbs about what medicare supplements plans are and why they should buy them. Feel free to play around with cool fonts and imagery, we want the site to be engaging!

Target Market(s)

seniors

Industry/Entity Type

Insurance

Number of Pages Required

1 page

Requirements
Must have
• Quiz, company name and tag line, script
Nice to have
• fun, engaging elements

```html
<!DOCTYPE html>
<html lang="en">
<head>
<meta charset="utf-8">
<title>Harborlight Plans</title>
<link href="https://fonts.googleapis.com/css2?family=Quicksand:wght@500;600;700&family=Open+Sans:wght@400;600&family=Arimo:wght@400&display=swap" rel="stylesheet">
<style>
:root{
  --teal:#1aa6c9;
  --teal-deep:#0f8fb5;
  --navy:#0c3f8a;
  --orange:#ef5a10;
  --tick:#f5901e;
  --pink:#ee0979;
  --red-orange:#f0501a;
  --ink:#1b1b1b;
  --grey:#555a60;
  --quiz-bg:#dcebf0;
  --white:#ffffff;
}
*{margin:0;padding:0;box-sizing:border-box}
html,body{width:1200px;height:2979px;overflow:hidden;background:var(--white)}
body{position:relative;font-family:'Open Sans',sans-serif;color:var(--ink)}
.abs{position:absolute}
.display{font-family:'Quicksand',sans-serif}

/* header */
.site-header{position:absolute;left:0;top:0;width:1200px;height:94px;background:var(--white)}
.brand{position:absolute;left:48px;top:30px;font:700 32px 'Quicksand',sans-serif;color:var(--teal-deep)}
.main-nav a{position:absolute;top:40px;font:500 18px 'Quicksand',sans-serif;color:var(--teal);text-decoration:none}
.main-nav a.current{color:var(--ink)}
.main-nav a.current::after{content:"";position:absolute;left:50%;bottom:-10px;width:22px;height:2px;margin-left:-11px;background:var(--teal)}

/* hero */
.hero{position:absolute;left:0;top:94px;width:1200px;height:566px;background:linear-gradient(90deg,#16acd0 0%,#3dbddb 35%,#a8dcea 55%,#d9e7ea 100%);overflow:hidden}
.hero-photo{position:absolute;left:560px;top:0;width:640px;height:566px;background:linear-gradient(90deg,rgba(200,230,238,0) 0%,rgba(150,160,170,.55) 45%,rgba(120,110,105,.7) 100%)}
.hero h1{position:absolute;left:102px;top:148px;font:700 51px 'Quicksand',sans-serif;color:var(--white);letter-spacing:.5px}
.hero .tagline{position:absolute;left:104px;top:214px;width:520px;font:500 23px/32px 'Quicksand',sans-serif;color:var(--white)}
.call-btn{position:absolute;left:95px;top:300px;width:362px;height:59px;border-radius:30px;background:var(--orange);color:var(--white);font:700 27px 'Quicksand',sans-serif;display:flex;align-items:center;justify-content:center;gap:6px}
.hero .call-note{position:absolute;left:124px;top:368px;font:700 19px 'Quicksand',sans-serif;color:var(--white)}

/* intro */
.intro{position:absolute;left:0;top:757px;width:1200px;text-align:center;font:400 21px/35px 'Arimo',sans-serif;color:var(--grey)}
.intro-cta{position:absolute;left:0;top:854px;width:1200px;text-align:center;font:400 21px/29px 'Arimo',sans-serif;color:var(--ink)}

/* quiz */
.quiz{position:absolute;left:0;top:993px;width:1200px;height:516px;background:linear-gradient(90deg,#d3e4ea,#e1eef2 50%,#d8e8ee)}
.quiz-notch{position:absolute;left:576px;top:993px}
.quiz h2{position:absolute;left:0;top:1046px;width:1200px;text-align:center;font:700 39px 'Quicksand',sans-serif;color:var(--navy)}
.quiz-col{position:absolute;top:1134px;font:400 19px 'Arimo',sans-serif;color:var(--ink)}
.quiz-col h3{font:400 25px 'Arimo',sans-serif;margin-bottom:14px}
.quiz-col label{display:flex;align-items:center;height:40px;gap:10px;margin-left:-2px}
.box{width:25px;height:25px;border:2px solid #6c8fa8;background:var(--white);border-radius:2px}
.zip{position:absolute;left:317px;top:1361px;width:566px;height:60px;border-radius:30px;background:var(--white);padding-left:37px;display:flex;align-items:center;font:400 19px 'Arimo',sans-serif;color:var(--ink);box-shadow:0 2px 6px rgba(0,0,0,.06)}

/* about plans */
.plans h2{position:absolute;left:0;top:1601px;width:1200px;text-align:center;font:500 35px 'Quicksand',sans-serif;color:var(--ink)}
.plans .lead{position:absolute;left:160px;top:1662px;width:880px;text-align:center;font:400 17.5px/27px 'Open Sans',sans-serif;color:var(--grey)}
.benefit{position:absolute;font:400 17.5px/27px 'Open Sans',sans-serif;color:var(--grey);padding-left:30px}
.benefit svg{position:absolute;left:0;top:5px}

/* costs */
.costs{position:absolute;left:0;top:2008px;width:1200px;height:739px;background:linear-gradient(100deg,var(--pink) 0%,#f0233e 50%,var(--red-orange) 100%);color:var(--white)}
.costs h2{position:absolute;left:0;top:88px;width:1200px;text-align:center;font:700 31px 'Quicksand',sans-serif}
.costs .lead{position:absolute;left:170px;top:152px;width:860px;text-align:center;font:400 18px/27px 'Open Sans',sans-serif}
.rating{position:absolute;top:330px;width:310px;text-align:center}
.rating .icon{width:64px;height:64px;margin:0 auto 20px;border:2px solid rgba(255,255,255,.85);border-radius:12px;background:rgba(255,255,255,.12)}
.rating h3{font:700 21px 'Quicksand',sans-serif;margin-bottom:12px}
.rating p{font:400 14.5px/23px 'Open Sans',sans-serif}
.costs .note{position:absolute;left:0;top:628px;width:1200px;text-align:center;font:400 16px/23px 'Open Sans',sans-serif}

/* footer */
.footer-nav a{position:absolute;top:2810px;font:500 19px 'Quicksand',sans-serif;color:var(--ink);text-decoration:none}
.copyright{position:absolute;left:0;top:2854px;width:1200px;text-align:center;font:400 14px 'Open Sans',sans-serif;color:var(--ink)}
.social{position:absolute;top:2896px;width:42px;height:42px;border:2px solid var(--navy);border-radius:50%}
</style>
</head>
<body>

<header class="site-header">
  <div class="brand">Harborlight Plans</div>
  <nav class="main-nav">
    <a class="current" style="left:477px">About</a>
    <a style="left:574px">Our Quiz</a>
    <a style="left:695px">Supplement Plan</a>
    <a style="left:885px">Blog</a>
    <a style="left:968px">Why Us</a>
    <a style="left:1075px">Contact</a>
  </nav>
</header>

<section class="hero">
  <div class="hero-photo" role="img" aria-label="Photo of a smiling woman sitting cross-legged in a chair using a laptop in a bright room"></div>
  <h1>Harborlight Plans</h1>
  <p class="tagline">Be confident in choosing the Medicare Supplement plan that’s right for you.</p>
  <div class="call-btn">
    <svg width="26" height="26" viewBox="0 0 24 24" fill="none" stroke="#fff" stroke-width="2" stroke-linecap="round" stroke-linejoin="round"><path d="M22 16.9v3a2 2 0 0 1-2.2 2 19.8 19.8 0 0 1-8.6-3.1 19.5 19.5 0 0 1-6-6A19.8 19.8 0 0 1 2.1 4.2 2 2 0 0 1 4.1 2h3a2 2 0 0 1 2 1.7c.1 1 .4 1.9.7 2.8a2 2 0 0 1-.5 2.1L8 9.9a16 16 0 0 0 6 6l1.3-1.3a2 2 0 0 1 2.1-.4c.9.3 1.8.6 2.8.7a2 2 0 0 1 1.7 2z"/></svg>
    Call (800) 555-0142
  </div>
  <p class="call-note">to talk to a live agent.</p>
</section>

<p class="intro">We know insurance can be confusing. With so much information and not enough answers, we’re here<br>to help you find the plan that works best for you, your family and your health.</p>
<p class="intro-cta">Take this short quiz to to find flexible and affordable plans<br>that you can feel confident in.</p>

<section class="quiz" role="img" aria-label="Faded photo of a smiling senior couple behind the quiz"></section>
<svg class="quiz-notch abs" width="48" height="24" viewBox="0 0 48 24"><path d="M0 0h48L24 24z" fill="#fff"/></svg>
<div class="quiz-content">
  <h2 class="abs" style="left:0;top:1046px;width:1200px;text-align:center;font:700 39px 'Quicksand',sans-serif;color:var(--navy)">Quiz Script</h2>
  <div class="quiz-col" style="left:178px">
    <h3>I am</h3>
    <label><span class="box"></span>a. Over 64 years old</label>
    <label><span class="box"></span>b. 64 years old</label>
    <label><span class="box"></span>c. Under 64 years old</label>
  </div>
  <div class="quiz-col" style="left:545px">
    <h3>I am</h3>
    <label><span class="box"></span>a. Male</label>
    <label><span class="box"></span>b. Female</label>
    <label><span class="box"></span>c. Unspecified</label>
  </div>
  <div class="quiz-col" style="left:858px">
    <h3>I want to see</h3>
    <label><span class="box"></span>a. Free plans</label>
    <label><span class="box"></span>b. Premium plans</label>
    <label><span class="box"></span>c. All plans</label>
  </div>
  <div class="zip">Enter Zip Code</div>
</div>

<section class="plans">
  <h2>What is a Medicare Supplement plan?</h2>
  <p class="lead">Each Medicare Supplement insurance plan offers a different level of basic benefits, but each lettered plan will include the same standardized basic benefits regardless of insurance company and location. Medicare Supplement insurance plans do not always cover vision, dental, long-term care, or hearing aids, but all plans must cover at least a portion of the following basic benefits:</p>
  <div class="benefit" style="left:106px;top:1812px;width:520px">
    <svg width="24" height="18" viewBox="0 0 24 18"><path d="M2 9l7 7L22 2" fill="none" stroke="#f5901e" stroke-width="3" stroke-linecap="round" stroke-linejoin="round"/></svg>
    Medicare Part A coinsurance costs up to an additional 365 days after Medicare benefits are exhausted</div>
  <div class="benefit" style="left:106px;top:1879px;width:520px">
    <svg width="24" height="18" viewBox="0 0 24 18"><path d="M2 9l7 7L22 2" fill="none" stroke="#f5901e" stroke-width="3" stroke-linecap="round" stroke-linejoin="round"/></svg>
    Medicare Part A hospice care coinsurance or copayments</div>
  <div class="benefit" style="left:655px;top:1812px;width:480px">
    <svg width="24" height="18" viewBox="0 0 24 18"><path d="M2 9l7 7L22 2" fill="none" stroke="#f5901e" stroke-width="3" stroke-linecap="round" stroke-linejoin="round"/></svg>
    Medicare Part B coinsurance or copayments</div>
  <div class="benefit" style="left:655px;top:1874px;width:480px">
    <svg width="24" height="18" viewBox="0 0 24 18"><path d="M2 9l7 7L22 2" fill="none" stroke="#f5901e" stroke-width="3" stroke-linecap="round" stroke-linejoin="round"/></svg>
    First three pints of blood used in a medical procedure</div>
</section>

<section class="costs">
  <h2>Medicare Supplement insurance plan costs</h2>
  <p class="lead">Although private insurance companies are required to offer the same basic benefits for each lettered plan, they do have the ability to charge different premiums. You might want to shop around to find a Medicare Supplement insurance plan that may fit your medical and financial needs. Insurance companies may price their plan premiums in any of the following ways:</p>
  <div class="rating" style="left:83px">
    <div class="icon" role="img" aria-label="Line icon of hands holding a group of people"></div>
    <h3>Community no-age-rated</h3>
    <p>These Medicare Supplement insurance plans charge premiums that are the same across the board, regardless of age.</p>
  </div>
  <div class="rating" style="left:442px">
    <div class="icon" role="img" aria-label="Line icon of a person with a document and gear"></div>
    <h3>Issue-age-rated</h3>
    <p>These plans base their premiums on your age when you first enrolled in the policy. Therefore, the younger you are when you enroll in this type of plan, the lower your premium will be.</p>
  </div>
  <div class="rating" style="left:835px">
    <div class="icon" role="img" aria-label="Line icon of a policy document with a shield"></div>
    <h3>Attained-age-rated</h3>
    <p>Like issue-age-rated, these plans base their premiums on the age you were when you first bought a policy, but unlike issue-age-rated, premiums increase as you get older.</p>
  </div>
  <p class="note">Please note that no matter what rating method an insurance company uses, premiums<br>may increase over time for reasons other than age, such as inflation.</p>
</section>

<footer>
  <nav class="footer-nav">
    <a style="left:254px">About</a>
    <a style="left:350px">Our Quiz</a>
    <a style="left:470px">Supplement Plan</a>
    <a style="left:661px">Blog</a>
    <a style="left:743px">Why Us</a>
    <a style="left:852px">Contact</a>
  </nav>
  <p class="copyright">© 2020 Company Name &nbsp;|&nbsp; All Rights Reserved &nbsp;|&nbsp; Disclaimer</p>
  <span class="social" style="left:503px" aria-label="Social link"></span>
  <span class="social" style="left:549px" aria-label="Social link"></span>
  <span class="social" style="left:595px" aria-label="Social link"></span>
  <span class="social" style="left:641px" aria-label="Social link"></span>
</footer>

</body>
</html>
```